Billboard design 8x3M RAVU (Spanish company)

We´re located in the south of Spain. We run a local telecom company.
We sell Fiber optic, and mobile phone lines mainly.
The billboard will have to be in Spanish, I would like the price to be something you spot on first sight when passing by in the car.
Our company color is blue, like in our logo which I will add. I will also add a example from what we currently have.
The new offer should be:
1000 megas + 100Gigas movil con llamadas ilimitadas. (meaning 1000Mb fiber optic speed and 100Gb data and unlimited calls for 1 mobile line)
Our details are: phone line 958 47 6620
Website: ra-vu.es

```html
<!DOCTYPE html>
<html lang="es">
<head>
<meta charset="utf-8">
<title>RAVU – Valla 8x3</title>
<link href="https://fonts.googleapis.com/css2?family=Poppins:ital,wght@0,500;0,600;0,700;0,800;1,600;1,700;1,800;1,900&display=swap" rel="stylesheet">
<style>
  :root {
    --stage: #4a4a4a;
    --blue-deep: #0626a8;
    --blue: #0c3bd0;
    --blue-bright: #1d55ea;
    --navy: #0a2a9c;
    --cyan: #1ec3f4;
    --yellow: #e3b10c;
    --red: #c00a0a;
    --white: #ffffff;
    --ink: #141414;
  }
  * { margin: 0; padding: 0; box-sizing: border-box; }
  html, body {
    width: 1200px; height: 1153px; overflow: hidden;
    background: var(--stage);
    font-family: "Poppins", Arial, sans-serif;
  }
  .billboard-frame {
    position: absolute; left: 40px; top: 366px;
    width: 1120px; height: 420px;
    box-shadow: 0 6px 18px rgba(0,0,0,.35);
  }
  .billboard {
    position: absolute; left: 0; top: 0;
    width: 1296px; height: 485px;
    transform: scale(0.8642); transform-origin: 0 0;
    overflow: hidden;
    background: radial-gradient(ellipse at 42% 45%, var(--blue-bright) 0%, var(--blue) 40%, var(--blue-deep) 100%);
  }
  .offer-panel { position: absolute; inset: 0; }
  .hero-art {
    position: absolute; left: 478px; top: 10px; width: 520px; height: 380px;
    border-radius: 40% 55% 45% 50%;
    background: radial-gradient(ellipse at 55% 40%, #6fa6f5 0%, #3a72e0 45%, rgba(30,80,220,0) 75%);
  }
  .brand { position: absolute; left: 108px; top: 30px; }
  .brand-name {
    font-weight: 800; font-size: 78px; line-height: 1; color: var(--cyan);
    letter-spacing: 4px;
  }
  .brand-services {
    margin-top: 6px; font-weight: 600; font-size: 22px; color: var(--cyan);
    letter-spacing: .3px;
  }
  .brand-services .light { color: var(--white); }
  .headline { position: absolute; left: 62px; top: 160px; font-style: italic; font-weight: 800; }
  .headline .line-fibra { font-size: 74px; line-height: 80px; color: var(--yellow); letter-spacing: -1px; }
  .headline .line-movil { font-size: 74px; line-height: 76px; color: var(--cyan); letter-spacing: -1px; }
  .headline .line-precio { font-size: 46px; line-height: 60px; color: var(--white); font-weight: 700; font-style: normal; }
  .phone-band {
    position: absolute; left: 0; top: 401px; width: 366px; height: 56px;
    background: var(--yellow); border-radius: 0 12px 12px 0;
    font-style: italic; font-weight: 800; font-size: 46px; line-height: 56px;
    color: var(--navy); text-align: right; padding-right: 22px; letter-spacing: -.5px;
  }
  .web {
    position: absolute; left: 390px; top: 400px;
    font-style: italic; font-weight: 800; font-size: 47px; line-height: 60px; color: var(--white);
  }
  .web .accent { color: var(--yellow); }
  .speed-badge {
    position: absolute; left: 905px; top: 0; width: 330px; height: 168px;
    background: var(--yellow); border-radius: 0 0 30px 30px;
    text-align: center; box-shadow: 0 6px 12px rgba(0,0,0,.15);
  }
  .speed-badge::after {
    content: ""; position: absolute; left: 150px; bottom: -14px;
    border-left: 10px solid transparent; border-right: 10px solid transparent;
    border-top: 14px solid var(--yellow);
  }
  .speed-badge .num { font-style: italic; font-weight: 900; font-size: 98px; line-height: 100px; color: var(--red); margin-top: 18px; letter-spacing: -2px; }
  .speed-badge .unit { font-style: italic; font-weight: 800; font-size: 36px; line-height: 36px; color: var(--navy); margin-top: -4px; }
  .data-line {
    position: absolute; left: 822px; top: 168px;
    font-style: italic; font-weight: 900; color: var(--navy); white-space: nowrap;
  }
  .data-line .big { font-size: 100px; line-height: 110px; letter-spacing: -4px; }
  .data-line .small { font-size: 42px; font-weight: 800; font-style: normal; margin-left: 4px; }
  .calls { position: absolute; left: 884px; top: 278px; display: flex; gap: 18px; align-items: center; }
  .calls p { font-style: italic; font-weight: 800; font-size: 26px; line-height: 32px; color: var(--ink); }
  .price { position: absolute; left: 920px; top: 340px; white-space: nowrap; }
  .price .por { font-style: italic; font-weight: 700; font-size: 28px; color: var(--ink); vertical-align: 34px; }
  .price .amount { font-style: italic; font-weight: 900; font-size: 104px; line-height: 110px; color: var(--red); letter-spacing: -2px; }
</style>
</head>
<body>
  <div class="billboard-frame">
    <section class="billboard" aria-label="Valla publicitaria RAVU">
      <svg class="offer-panel" width="1296" height="485" viewBox="0 0 1296 485" aria-hidden="true">
        <path d="M880 0 C 820 40, 700 90, 760 200 C 820 320, 760 400, 840 440 C 900 470, 980 470, 1010 485 L1296 485 L1296 0 Z" fill="#0a2fb8"/>
        <path d="M905 0 C 845 45, 735 100, 790 205 C 845 315, 790 395, 860 430 C 915 458, 985 462, 1012 485 L1296 485 L1296 0 Z" fill="var(--white)"/>
        <path d="M820 420 C 900 380, 960 440, 1030 420" fill="none" stroke="#e6e9f0" stroke-width="10"/>
      </svg>

      <div class="hero-art" role="img" aria-label="Ilustración de un cohete azul despegando desde la pantalla de un portátil con nube de humo"></div>

      <div class="brand">
        <div class="brand-name">RAVU</div>
        <div class="brand-services">Wifi | Fibra | <span class="light">Movil | Tv</span></div>
      </div>

      <div class="headline">
        <div class="line-fibra">TU FIBRA</div>
        <div class="line-movil">+ MÓVIL</div>
        <div class="line-precio">AL MEJORPRECIO</div>
      </div>

      <div class="phone-band">958 47 6620</div>
      <div class="web">www.<span class="accent">ra-vu</span>.es</div>

      <div class="speed-badge">
        <div class="num">1000</div>
        <div class="unit">MEGAS</div>
      </div>

      <div class="data-line"><span class="big">+100</span><span class="small">GIGAS</span></div>

      <div class="calls">
        <svg width="24" height="44" viewBox="0 0 24 44" aria-label="móvil" role="img">
          <rect x="2" y="2" width="20" height="40" rx="4" fill="none" stroke="var(--yellow)" stroke-width="3"/>
          <line x1="9" y1="36" x2="15" y2="36" stroke="var(--yellow)" stroke-width="3" stroke-linecap="round"/>
        </svg>
        <p>movil con llamadas<br>ilimitadas.</p>
      </div>

      <div class="price"><span class="por">por </span><span class="amount">35€</span></div>
    </section>
  </div>
</body>
</html>
```